Upmarket Dessert Lounge needs a Business Card Design

We are an upmarket dessert lounge needing a business card to match our image.

We want something that is simple yet beautiful, feminine, classy, sophisticated and elegant. We want it to stand out and don't mind if it is bold.

The design should include our logo and colours of red or maroon with gold highlights. We don't mind if black is used.

Marlow & Quince

Target Market(s)

For those who like to indulge or treat themselves and give in to their temptations on good quality desserts.

Industry/Entity Type

Business

Requirements
Must have
• Must include our logo and our name

Marlow & Quince

M & Q

```html
<!DOCTYPE html>
<html lang="en">
<head>
<meta charset="utf-8">
<title>Marlow &amp; Quince – Business Card</title>
<link rel="stylesheet" href="https://fonts.googleapis.com/css2?family=Cormorant+Garamond:wght@500;600;700&family=Open+Sans:wght@400;600&display=swap">
<style>
  :root {
    --maroon: #7a1416;
    --maroon-deep: #5e0e10;
    --gold: #f6d9a6;
    --gold-line: #f1d3a0;
    --paper: #ffffff;
    --ink: #3a3a3a;
    --stage: #ece8e3;
    --serif: "Cormorant Garamond", Georgia, serif;
    --sans: "Open Sans", Arial, sans-serif;
  }
  * { box-sizing: border-box; margin: 0; padding: 0; }
  html, body { width: 1200px; height: 758px; overflow: hidden; }
  body {
    background: var(--stage);
    display: flex;
    align-items: center;
    justify-content: center;
    gap: 60px;
    font-family: var(--sans);
  }
  .card {
    position: relative;
    width: 520px;
    height: 300px;
    border-radius: 22px;
    overflow: hidden;
    box-shadow: 0 10px 28px rgba(0,0,0,0.25);
  }
  /* Front */
  .card-front { background: var(--maroon); }
  .front-top {
    position: absolute; left: 0; top: 0; width: 100%; height: 168px;
    background: var(--paper);
    border-bottom: 3px solid var(--gold-line);
  }
  .brand-name {
    position: absolute; left: 0; right: 0; top: 62px;
    text-align: center;
    font-family: var(--serif);
    font-weight: 600;
    font-size: 34px;
    letter-spacing: 2px;
    color: var(--maroon);
  }
  .name-tab {
    position: absolute; left: 150px; top: 171px;
    width: 290px; height: 42px;
    background: var(--paper);
    display: flex; align-items: center; justify-content: center; gap: 6px;
  }
  .name-tab .person {
    font-family: var(--serif); font-weight: 700; font-size: 20px; color: var(--maroon);
  }
  .name-tab .role {
    font-family: var(--sans); font-size: 12px; color: var(--ink);
  }
  .address {
    position: absolute; right: 290px; top: 240px;
    text-align: right; color: var(--paper);
    font-size: 12.5px; line-height: 18px;
  }
  .divider {
    position: absolute; left: 244px; top: 222px;
    width: 1px; height: 66px; background: rgba(255,255,255,0.55);
  }
  .contacts {
    position: absolute; left: 256px; top: 222px;
    list-style: none; color: var(--paper);
    font-size: 12.5px; line-height: 17px;
  }
  .contacts li { display: flex; align-items: center; gap: 5px; }
  .contacts svg { width: 10px; height: 10px; fill: var(--paper); flex: none; }
  /* Back */
  .card-back {
    background: var(--maroon);
    display: flex; flex-direction: column; align-items: center;
  }
  .monogram {
    margin-top: 58px;
    font-family: var(--serif);
    font-weight: 600;
    font-size: 92px;
    line-height: 1;
    color: var(--gold);
  }
  .back-web {
    margin-top: 52px;
    font-family: var(--sans);
    font-size: 19px;
    letter-spacing: 3px;
    color: var(--paper);
  }
</style>
</head>
<body>
  <article class="card card-front">
    <div class="front-top">
      <div class="brand-name">MARLOW &amp; QUINCE</div>
    </div>
    <div class="name-tab">
      <span class="person">Your name,</span><span class="role">Title</span>
    </div>
    <address class="address">Street Name, City Name<br>State Zip Code</address>
    <div class="divider"></div>
    <ul class="contacts">
      <li><svg viewBox="0 0 10 10" aria-hidden="true"><path d="M2 0.5l2 2-1 1.2c.6 1.3 1.7 2.4 3 3l1.2-1 2 2-1.2 1.8C4.5 9.3.7 5.5.2 1.7z"/></svg>555-014-2368</li>
      <li><svg viewBox="0 0 10 10" aria-hidden="true"><path d="M2.5 0h5v10h-5zM3.3 1v6.6h3.4V1z"/></svg>555-014-2368</li>
      <li><svg viewBox="0 0 10 10" aria-hidden="true"><path d="M0 2h10v6H0zM.8 2.6 5 5.6l4.2-3z" fill-rule="evenodd"/></svg>info@marlowquince.com</li>
      <li><svg viewBox="0 0 10 10" aria-hidden="true"><circle cx="5" cy="5" r="4.5"/><path d="M.5 5h9M5 .5c-2.4 2.5-2.4 6.5 0 9M5 .5c2.4 2.5 2.4 6.5 0 9" stroke="#7a1416" stroke-width=".7" fill="none"/></svg>www.marlowquince.com</li>
    </ul>
  </article>

  <article class="card card-back">
    <div class="monogram">M &amp; Q</div>
    <div class="back-web">www.marlowquince.com</div>
  </article>
</body>
</html>
```